Flyer needed For the Council for Stewardship in Civic Ventures

With an increasing need for professional staffing in our design and construction industry it is important for organizations to be able to attract, support, and retain people of all genders. With the increase of women entering the design/construction industry, we need to be able to identify and address the specific needs of women in our industry, including those A/E’s who are on the facility Owner side.

This Forum will provide a venue to openly discuss the issues affecting our industry and ideas to address those issues.The program includes time for presentations and a panel discussion by accomplished women in our industry, and facilitated table and open discussions to form solutions with your peers. You will come away with ideas you can implement within your organization to build processes and a supportive culture for women

IN THE ATTACHMENTS
* you'll find our company logo

Target Market(s)

Women in the design and construction industry

Industry/Entity Type

Construction

Requirements
Must have
• Logo, event name, date, time, location, panelists names and pics, PBQ continuing education provided, contact information: Doreen Haskwell, doreen.haskwell@c-scvx.org, (512) 847-3096
• Register at: www.c-scvx.org/events
• Design should encompass the description given above.
Nice to have
• Colors that compliment our logo

```html
<!DOCTYPE html>
<html lang="en">
<head>
<meta charset="utf-8">
<title>AEC Industry Women's Mini-Forum &amp; Workshop</title>
<link rel="stylesheet" href="https://fonts.googleapis.com/css2?family=Antonio:wght@300;400;600;700&family=PT+Sans:wght@400;700&display=swap">
<style>
  :root {
    --green-top: #3e9300;
    --green-mid: #7dbb4a;
    --green-pale: #c9e2a8;
    --paper: #f7f9f2;
    --navy: #1f3a8f;
    --lime: #e6f45c;
    --slate: #56595c;
    --olive: #8cb03c;
    --olive-text: #5b6b36;
    --disc: rgba(66, 110, 118, 0.55);
    --disc-low: rgba(95, 140, 120, 0.35);
    --badge: #0c0c0c;
  }
  * { margin: 0; padding: 0; box-sizing: border-box; }
  html, body { width: 857px; height: 1200px; overflow: hidden; }
  body { font-family: "PT Sans", sans-serif; }
  .flyer {
    position: relative;
    width: 857px;
    height: 1200px;
    overflow: hidden;
    background: linear-gradient(180deg, var(--green-top) 0%, #55a416 38%, var(--green-mid) 60%, var(--green-pale) 78%, var(--paper) 100%);
  }
  .backdrop { position: absolute; inset: 0; }
  .brand {
    position: absolute;
    left: 22px; top: 34px;
    display: flex; align-items: center; gap: 14px;
  }
  .brand-dot {
    width: 84px; height: 84px; border-radius: 50%;
    background: #2e59a8;
  }
  .brand-name {
    font-family: "PT Sans", sans-serif;
    font-weight: 700;
    font-size: 19px;
    line-height: 1.15;
    color: var(--lime);
    width: 230px;
  }
  .accreditation-badge {
    position: absolute;
    left: 787px; top: 61px;
    width: 58px; height: 66px;
    background: var(--badge);
  }
  .headline { position: absolute; left: 0; width: 857px; text-align: center; white-space: nowrap; }
  .event-industry {
    top: 140px;
    font-family: "Antonio", sans-serif;
    font-weight: 700;
    font-size: 80px;
    line-height: 1;
    color: var(--navy);
    letter-spacing: 0.02em;
  }
  .event-name {
    top: 226px;
    font-family: "Antonio", sans-serif;
    font-weight: 400;
    font-size: 56px;
    line-height: 1;
    color: var(--lime);
    letter-spacing: 0.08em;
  }
  .event-name span { display: inline-block; transform: scaleX(0.74); transform-origin: center; }
  .event-date {
    top: 300px;
    font-family: "Antonio", sans-serif;
    font-weight: 600;
    font-size: 44px;
    line-height: 1;
    color: var(--navy);
  }
  .event-venue {
    top: 358px;
    font-family: "Antonio", sans-serif;
    font-weight: 400;
    font-size: 29px;
    line-height: 1;
    color: var(--lime);
    letter-spacing: 0.14em;
  }
  .program {
    position: absolute;
    left: 0; top: 413px; width: 900px;
    text-align: center;
    font-size: 20.5px;
    line-height: 27.9px;
    color: var(--navy);
  }
  .accreditation {
    position: absolute;
    left: 0; top: 885px; width: 874px;
    text-align: center;
    font-size: 53px;
    line-height: 1;
    color: var(--navy);
  }
  .contact {
    position: absolute;
    left: 0; top: 989px; width: 861px;
    text-align: center;
    color: var(--olive-text);
  }
  .contact-name { font-weight: 700; font-size: 27px; color: var(--slate); line-height: 1; }
  .contact-line { font-size: 22px; line-height: 1; margin-top: 22px; }
  .register {
    position: absolute;
    left: 0; top: 1146px; width: 860px;
    text-align: center;
    font-size: 28px;
    line-height: 1;
    color: var(--slate);
  }
</style>
</head>
<body>
<main class="flyer">
  <svg class="backdrop" width="857" height="1200" viewBox="0 0 857 1200" aria-hidden="true">
    <defs>
      <clipPath id="disc-clip"><rect x="0" y="0" width="857" height="712"/></clipPath>
    </defs>
    <g clip-path="url(#disc-clip)">
      <circle cx="431" cy="500" r="382" fill="var(--disc)"/>
    </g>
    <path d="M52 490 Q431 610 812 490 L812 520 Q760 660 745 712 L124 712 Q95 640 52 520 Z" fill="var(--disc-low)"/>
    <path d="M3 1078 Q430 850 854 1078 L660 1023 Q640 1130 430 1130 Q220 1130 196 1023 Z" fill="var(--olive)"/>
    <path d="M3 1078 Q430 824 854 1078 Q430 850 3 1078 Z" fill="var(--slate)"/>
  </svg>

  <header class="brand">
    <span class="brand-dot"></span>
    <span class="brand-name">Council for Stewardship in Civic Ventures</span>
  </header>
  <div class="accreditation-badge" role="img" aria-label="Continuing education badge"></div>

  <h1 class="headline event-industry">AEC INDUSTRY</h1>
  <h2 class="headline event-name"><span>Women's Mini-Forum &amp; Workshop</span></h2>
  <p class="headline event-date">JANUARY 13, 2016</p>
  <p class="headline event-venue">Meridian Suites, San Marcos, Texas</p>

  <p class="program">
    The program includes time for presentations<br>
    and a panel discussion by<br>
    accomplished women in our industry,<br>
    and facilitated table and open discussions to form<br>
    solutions with your peers.<br>
    You will come away with ideas you can implement<br>
    within your organization<br>
    to build processes and a supportive culture for women.<br>
    A visual note-taker and separate scribe<br>
    will be utilized to compile ideas and solutions,<br>
    for distribution to participants after the event.<br>
    Presenters and Panelists: architect, engineer,<br>
    contractor, sub/trade, facility Owner<br>
    Table Facilitators:&nbsp; one for each table,<br>
    with tables divided into industry segments:<br>
    architects, engineers, contractors, subs/trades, Owners.
  </p>

  <p class="accreditation">PBQ continuing education</p>

  <section class="contact">
    <p class="contact-name">Contact : Doreen Haskwell</p>
    <p class="contact-line">doreen.haskwell@c-scvx.org</p>
    <p class="contact-line">(512) 847-3096</p>
  </section>

  <p class="register">Register at: www.c-scvx.org/events</p>
</main>
</body>
</html>
```